7' x 4' sign for a new multiunit residential mountain location**

Our mission is to build people their dream home through the use of professional and thoughtful design. We're a new developer, building a new and feature-filled fourplex, and need a brand and presence that generates interests and builds our brand. Our homes are professionally and thoughtfully designed - we agonize over the details so our homeowners don't have to once they move in.

We're constructing a new fourplex in downtown Larchmere, BC, Canada. The location is in the heart of the city's entertainment and cultural zones, is surrounded by mountains and a lake, and within an hour of over 100 wineries. "Valley" residents prize their time outdoors - boating, biking, hiking, skiing, and more. It's no wonder Kelowna is often cited as one of the most beautiful and desirable places to live in the world.

attachments - brand elements, rendering of the unit, feature sheet for each unit, and picture of the sign casing (7' wide and 4' long envelop - pic of sign frame attached).

Target Market(s)

Young professionals (age 30 to 45); Empty nestes (age 55+)

Font styles to use
Other font styles liked:
• Cordia New

Requirements
Must have
• Our tag line - Living, by Intent

Presence - this is an unusual shape and large sign. It must create interest and build our brand.

```html
<!DOCTYPE html>
<html lang="en">
<head>
<meta charset="UTF-8">
<title>217 Harlow — Living, by Intent</title>
<link rel="stylesheet" href="https://fonts.googleapis.com/css2?family=Cormorant+Garamond:wght@500;600&display=swap">
<style>
  :root {
    --sign-centre: #6a3f34;
    --sign-mid: #47272a;
    --sign-edge: #221014;
    --gold-light: #f1e9c2;
    --gold: #cfc08a;
    --gold-deep: #a8955c;
  }
  * { margin: 0; padding: 0; box-sizing: border-box; }
  html, body {
    width: 1200px;
    height: 667px;
    overflow: hidden;
  }
  .sign {
    position: relative;
    width: 1200px;
    height: 667px;
    background: radial-gradient(ellipse 55% 75% at 50% 52%, var(--sign-centre) 0%, var(--sign-mid) 55%, var(--sign-edge) 100%);
    font-family: "Cormorant Garamond", "Times New Roman", serif;
    font-variant-numeric: lining-nums;
    text-align: center;
  }
  .gold-text {
    background: linear-gradient(180deg, var(--gold-light) 0%, var(--gold) 55%, var(--gold-deep) 100%);
    -webkit-background-clip: text;
    background-clip: text;
    color: transparent;
  }
  .sign__address {
    position: absolute;
    top: 64px;
    left: 0;
    width: 100%;
    font-size: 176px;
    font-weight: 600;
    line-height: 1;
    letter-spacing: 4px;
    white-space: nowrap;
  }
  .sign__divider {
    position: absolute;
    top: 317px;
    left: 0;
    width: 100%;
    height: 2px;
  }
  .sign__rule {
    position: absolute;
    top: 0;
    height: 2px;
    background: var(--gold);
  }
  .sign__rule--left { left: 85px; width: 454px; }
  .sign__rule--right { left: 665px; width: 459px; }
  .sign__ornament {
    position: absolute;
    top: 280px;
    left: 564px;
    width: 76px;
    height: 76px;
    border-radius: 50%;
    background: radial-gradient(circle, rgba(207,192,138,0.5) 0%, rgba(207,192,138,0.15) 60%, rgba(207,192,138,0) 75%);
  }
  .sign__tagline {
    position: absolute;
    top: 400px;
    left: 0;
    width: 100%;
    font-size: 96px;
    font-weight: 600;
    line-height: 1;
    letter-spacing: 1px;
    white-space: nowrap;
  }
  .sign__location {
    position: absolute;
    top: 517px;
    left: 0;
    width: 100%;
    font-size: 60px;
    font-weight: 600;
    line-height: 1;
    letter-spacing: 1px;
    white-space: nowrap;
  }
</style>
</head>
<body>
  <main class="sign">
    <h1 class="sign__address gold-text">217 HARLOW</h1>
    <div class="sign__divider">
      <span class="sign__rule sign__rule--left"></span>
      <span class="sign__rule sign__rule--right"></span>
    </div>
    <div class="sign__ornament" role="img" aria-label="Gold four-petal flourish ornament centred on the divider"></div>
    <p class="sign__tagline gold-text">LIVING, BY INTENT</p>
    <p class="sign__location gold-text">Larchmere, BC, Canada</p>
  </main>
</body>
</html>
```